Marine Services Letterhead design

We need a letterhead design for an Australian owned company in Victoria named K+T Harbour Works Pty Ltd. We provide linesmen and launches to assist the large ships that come into port.
Our colour is orange.
The final design should have a strong nautical theme and communicate safety and reliability.
I would like to use the letter head on invoices so it should print to pdf well.

Target Market(s)

Owners and representatives of shipping companies. It is not for general public

Industry/Entity Type

Nautical

Requirements
Must have
• A shipping theme, not overly complicated, featuring safety orange colours but not all orange of course.
The letterhead should just sit at the top of the page so I can use for invoices.
Nice to have
• Something elegant and stylish
Should not have
• cartoons or pop art

```html
<!DOCTYPE html>
<html lang="en">
<head>
<meta charset="utf-8">
<title>K+T Harbour Works Pty Ltd — Letterhead</title>
<link rel="stylesheet" href="https://fonts.googleapis.com/css2?family=Cinzel:wght@500&family=Open+Sans:wght@400&display=swap">
<style>
  :root {
    --paper: #ffffff;
    --ink: #1f2623;
    --sea-green: #8fc6a2;
    --icon-green: #6fb68a;
    --safety-orange: #e9a23e;
  }
  * { margin: 0; padding: 0; box-sizing: border-box; }
  html, body { width: 880px; height: 1200px; overflow: hidden; background: var(--paper); }
  .letterhead {
    position: relative;
    width: 880px;
    height: 1200px;
    background: var(--paper);
  }
  .brand {
    position: absolute;
    left: 64px;
    top: 96px;
    display: flex;
    align-items: center;
    gap: 16px;
  }
  .brand-square {
    width: 40px;
    height: 40px;
    background: var(--safety-orange);
  }
  .brand-name {
    font-family: "Cinzel", serif;
    font-weight: 500;
    font-size: 24px;
    color: var(--ink);
    letter-spacing: 0.5px;
  }
  .contact {
    position: absolute;
    left: 632px;
    top: 74px;
    list-style: none;
    font-family: "Open Sans", sans-serif;
    font-size: 16px;
    color: var(--ink);
    line-height: 31px;
  }
  .contact li { display: flex; align-items: center; gap: 4px; }
  .contact svg { width: 12px; height: 14px; fill: var(--icon-green); }
  .contact .abn { padding-left: 4px; }
  .footer-band {
    position: absolute;
    left: 0;
    bottom: 0;
    width: 880px;
    height: 136px;
    display: flex;
    align-items: center;
    justify-content: center;
  }
  .wave-pattern {
    position: absolute;
    inset: 0;
    background: var(--sea-green);
  }
  .footer-name {
    position: relative;
    font-family: "Cinzel", serif;
    font-weight: 500;
    font-size: 30px;
    color: var(--ink);
    letter-spacing: 1px;
  }
</style>
</head>
<body>
  <main class="letterhead">
    <header>
      <div class="brand">
        <div class="brand-square"></div>
        <span class="brand-name">K+T Harbour Works</span>
      </div>
      <ul class="contact">
        <li>
          <svg viewBox="0 0 12 14" aria-hidden="true"><path d="M6 0C3 0 1 2.2 1 5c0 3.5 5 9 5 9s5-5.5 5-9c0-2.8-2-5-5-5zm0 7a2 2 0 1 1 0-4 2 2 0 0 1 0 4z"/></svg>
          PO Box 412 Harbourvale 3990
        </li>
        <li>
          <svg viewBox="0 0 12 14" aria-hidden="true"><path d="M4 1 2 2C0.5 3 1 7 3 10s5 4.5 6.5 3.5l1.5-1.5-2.5-2.5-1.5 1C5.8 10 4.2 7.5 4.3 6L5.8 5z"/></svg>
          1300 555 018
        </li>
        <li class="abn">ABN: 48120395716</li>
      </ul>
    </header>
    <footer class="footer-band">
      <div class="wave-pattern" role="img" aria-label="Band of soft cream wavy lines across a sea green strip"></div>
      <span class="footer-name">K+T Harbour Works Pty Ltd</span>
    </footer>
  </main>
</body>
</html>
```